Website Design for R W Builders: Showcasing Excellence in General Contracting

R W Builders, a leading general contractor based in California, is seeking a professional and engaging website design to effectively showcase our expertise, services, and commitment to excellence. The website will serve as a digital platform to represent our brand identity, highlight our portfolio, and attract potential clients in various sectors.

Key Objectives:

Reflect Company Identity: The website should accurately reflect the identity and values of R W Builders, including our dedication to quality, professionalism, and client satisfaction.
Showcase Services: Highlight our wide range of general contracting services, including but not limited to construction management, design-build, renovation, and commercial construction.
Portfolio Display: Display an extensive portfolio of past projects completed by R W Builders, showcasing our capabilities, craftsmanship, and successful outcomes.
Client Testimonials: Incorporate client testimonials and case studies to demonstrate our track record of delivering projects on time, within budget, and to the highest standards.
Contact Information: Ensure easy access to contact information, including phone number, email, and physical address, to facilitate communication with potential clients.
Responsive Design: Develop a responsive website design optimized for various devices and screen sizes, ensuring a seamless user experience across desktops, laptops, tablets, and smartphones.
Search Engine Optimization (SEO): Implement SEO best practices to enhance the visibility of the website on search engines, increasing organic traffic and generating leads.
User-Friendly Navigation: Create an intuitive and user-friendly navigation structure that enables visitors to easily find the information they need, such as services, portfolio, testimonials, and contact details.
Visual Appeal: Utilize visually appealing graphics, images, and layout designs to capture the attention of visitors and leave a lasting impression of professionalism and quality.
Compliance and Security: Ensure compliance with industry standards and regulations, as well as implementing necessary security measures to protect user data and privacy.

```html
<!DOCTYPE html>
<html lang="en">
<head>
<meta charset="utf-8">
<title>R W Builders — General Contracting</title>
<link href="https://fonts.googleapis.com/css2?family=Montserrat:ital,wght@0,400;0,500;0,600;0,700;0,800;1,600&display=swap" rel="stylesheet">
<style>
:root{
  --blue:#12a5e6;
  --blue-dark:#0a8fd0;
  --navy:#0b1a33;
  --ink:#111;
  --muted:#777;
  --cream:#f9f8f6;
  --white:#fff;
}
*{box-sizing:border-box;margin:0;padding:0}
html,body{width:1200px;height:4313px;overflow:hidden}
body{position:relative;background:var(--white);font-family:'Montserrat',sans-serif;color:var(--ink)}
.abs{position:absolute}
.btn{position:absolute;display:flex;align-items:center;justify-content:center;background:var(--blue);color:var(--white);font-weight:700;font-size:15px;border-radius:6px}
.section-title{position:absolute;left:0;width:1200px;text-align:center;font-weight:800;font-size:37px;color:var(--ink)}

/* header */
.topbar{left:0;top:0;width:1200px;height:101px;background:var(--blue);z-index:3}
.nav a{position:absolute;top:42px;color:var(--white);font-size:13px;font-weight:600;text-decoration:none}
.brand{position:absolute;left:530px;top:20px;width:140px;height:142px;border-radius:50%;background:var(--blue);display:flex;align-items:flex-end;justify-content:center;padding-bottom:14px;z-index:4}
.brand-inner{width:122px;height:122px;border-radius:50%;background:var(--white);display:flex;align-items:center;justify-content:center;text-align:center;font-weight:800;font-size:17px;color:var(--ink);line-height:1.1}
.call-icon{left:929px;top:29px;width:46px;height:46px;border-radius:50%;background:var(--white);display:flex;align-items:center;justify-content:center}
.call-label{left:994px;top:22px;font-size:14px;font-weight:700;color:var(--white)}
.call-number{left:996px;top:48px;font-size:22px;font-weight:700;color:var(--white);letter-spacing:.5px}
.slash{left:940px;top:0;width:2px;height:110px;background:var(--white);transform:rotate(12deg);transform-origin:top;opacity:.9}

/* hero */
.hero{left:0;top:101px;width:1200px;height:620px}
.hero-photo{position:absolute;inset:0;background:linear-gradient(90deg,#2a2622 0%,#5a4a3c 35%,#8c7a66 60%,#b7a48d 100%)}
.hero-shade{position:absolute;inset:0;background:linear-gradient(90deg,rgba(0,0,0,.55),rgba(0,0,0,0) 60%)}
.hero-copy{position:absolute;left:109px;top:106px;width:420px;color:var(--white)}
.hero-copy .eyebrow{font-size:23px;font-weight:700}
.hero-copy h1{font-size:44px;font-weight:800;margin-top:4px}
.hero-copy p{font-size:20px;line-height:38px;margin-top:10px;font-weight:500}
.hero svg{position:absolute;left:0;top:0}

/* about */
.about{left:0;top:812px;width:1200px;height:628px;background:var(--cream)}
.about-text{left:208px;top:885px;width:785px;text-align:center;font-size:13px;line-height:28px;color:var(--muted)}
.about-art{left:20px;top:1167px;width:1160px;height:273px;background:radial-gradient(ellipse at 50% 60%,#8b7a66 0%,#c9a77e 35%,#dfe7ee 70%,#ffffff 100%)}

/* services */
.tabs{left:167px;top:1604px;width:864px;height:63px;background:var(--white);box-shadow:0 2px 8px rgba(0,0,0,.15);display:flex}
.tab{flex:1;display:flex;align-items:center;padding-left:30px;font-size:24px;font-weight:500}
.tab.active{background:var(--blue);color:var(--white);padding-left:30px}
.tab.plain{padding-left:36px;color:var(--ink)}
.card{position:absolute;width:308px;height:322px;background:var(--white);box-shadow:0 2px 10px rgba(0,0,0,.14)}
.card .photo{position:absolute;left:8px;top:8px;width:292px;height:196px}
.card .badge{position:absolute;left:114px;top:161px;width:80px;height:80px;border-radius:50%;background:var(--blue);border:5px solid var(--white);display:flex;align-items:center;justify-content:center}
.card .label{position:absolute;left:0;width:100%;top:267px;text-align:center;font-size:22px;font-weight:600}

/* portfolio */
.portfolio{left:0;top:2478px;width:1200px;height:792px;background:linear-gradient(180deg,var(--blue) 0%,#19a9e8 100%)}
.portfolio svg{position:absolute;left:0;top:0}
.pf-photo{position:absolute;height:274px}
.pf-caption{position:absolute;border-left:3px solid var(--white);padding-left:12px;color:var(--white);font-size:20px;font-weight:700;line-height:32px;width:370px}
.arrow{position:absolute;width:54px;height:54px;border-radius:50%;background:var(--white);display:flex;align-items:center;justify-content:center}

/* testimonials */
.quote-card{position:absolute;top:3482px;width:323px;height:226px;background:var(--white);box-shadow:0 3px 12px rgba(0,0,0,.16)}
.quote-mark{position:absolute;left:15px;top:-38px;width:74px;height:74px;border-radius:50%;background:var(--blue);display:flex;align-items:center;justify-content:center}
.quote-text{position:absolute;left:29px;top:52px;width:270px;font-size:13px;line-height:25px;color:var(--muted)}
.quote-name{position:absolute;left:29px;top:164px;font-size:16px;font-weight:600;font-style:italic}
.quote-loc{position:absolute;left:29px;top:190px;font-size:13px;color:var(--blue)}
.dots{left:514px;top:3773px;display:flex;gap:10px}
.dots span{width:35px;height:4px;background:#b9ddf3;border-radius:2px}
.dots span.on{background:var(--blue)}

/* footer */
.footer{left:0;top:3850px;width:1200px;height:463px;background:var(--navy);color:var(--white)}
.foot-brand{left:109px;top:3960px;font-size:30px;font-weight:800;color:var(--white);display:flex;align-items:center;gap:12px}
.foot-brand i{display:block;width:22px;height:22px;border-radius:50%;background:var(--blue)}
.foot-col h4{position:absolute;top:3934px;font-size:21px;font-weight:600}
.foot-links{position:absolute;top:3990px;font-size:14px;line-height:30px;list-style:none}
.contact-list{position:absolute;left:882px;top:3988px;font-size:14px;line-height:28px}
.contact-list b{font-weight:700;display:flex;align-items:center;gap:6px}
.contact-list div{padding-left:20px}
.rule{left:109px;top:4250px;width:976px;height:1px;background:rgba(255,255,255,.7)}
.copyright{left:0;width:1200px;top:4270px;text-align:center;font-size:14px}
</style>
</head>
<body>

<header class="abs topbar">
  <nav class="nav">
    <a style="left:122px">HOME</a>
    <a style="left:204px">ABOUT US</a>
    <a style="left:310px">SERVICES</a>
    <a style="left:410px">PORTFOLIO</a>
    <a style="left:695px">TESTIMONIALS</a>
    <a style="left:834px">CONTACT</a>
  </nav>
  <div class="abs slash"></div>
  <div class="abs call-icon">
    <svg width="22" height="22" viewBox="0 0 24 24"><path fill="#111" d="M6.6 10.8a15 15 0 0 0 6.6 6.6l2.2-2.2a1 1 0 0 1 1-.25 11.4 11.4 0 0 0 3.6.57 1 1 0 0 1 1 1V20a1 1 0 0 1-1 1A17 17 0 0 1 3 4a1 1 0 0 1 1-1h3.5a1 1 0 0 1 1 1c0 1.25.2 2.45.57 3.57a1 1 0 0 1-.25 1z"/></svg>
  </div>
  <div class="abs call-label">Call Today For Service</div>
  <div class="abs call-number">(805) 555-0142</div>
</header>
<div class="brand"><div class="brand-inner">R W<br>Builders</div></div>

<section class="abs hero">
  <div class="hero-photo" role="img" aria-label="Two engineers in hard hats reviewing plans on a construction site"></div>
  <div class="hero-shade"></div>
  <div class="hero-copy">
    <div class="eyebrow">WELCOME TO</div>
    <h1>R W BUILDERS</h1>
    <p>Since 2013, R W Builders has been a thriving 8(a) certified General Contractor, consistently delivering successful projects to adiverse array of clients.</p>
  </div>
  <a class="btn" style="left:110px;top:361px;width:173px;height:43px">Get Started</a>
  <svg width="1200" height="620" viewBox="0 0 1200 620">
    <path fill="#12a5e6" d="M0 478 C 300 610, 640 640, 1200 420 L1200 620 L0 620Z"/>
    <path fill="#fff" d="M0 496 C 300 625, 640 655, 1200 445 L1200 620 L0 620Z"/>
  </svg>
</section>

<section class="abs about"></section>
<h2 class="section-title" style="top:820px">ABOUT US</h2>
<p class="abs about-text">Lorem Ipsum is simply dummy text of the printing and typesetting industry. Lorem Ipsum has been the industry's standard dummy text ever since the 1500s, when an unknown printer took a galley of type and scrambled it to make a type specimen book. It has survived not only five centuries, but also the leap into electronic typesetting, remaining essentially unchanged.Lorem Ipsum is simply dummy text of the printing and typesetting industry. Lorem Ipsum has been the industry's standard dummy text ever since the 1500s, when an unknown printer took a galley of type and scrambled it to make a type specimen book. It has survived not only five centuries, but also the leap into electronic typesetting, remaining essentially</p>
<a class="btn" style="left:512px;top:1086px;width:173px;height:47px">Read More</a>
<div class="abs about-art" role="img" aria-label="Watercolor illustration of workers in hard hats facing a city skyline"></div>

<h2 class="section-title" style="top:1524px">OUR SERVICES</h2>
<div class="abs tabs">
  <div class="tab active">Specialized Services</div>
  <div class="tab plain">General Contracting</div>
</div>

<div class="card" style="left:110px;top:1709px">
  <div class="photo" role="img" aria-label="Building under construction with cranes" style="background:linear-gradient(180deg,#b9cfe2,#8d8478)"></div>
  <div class="badge"><svg width="34" height="34" viewBox="0 0 24 24" fill="none" stroke="#111" stroke-width="1.5"><path d="M12 3 2 20h20z"/><circle cx="12" cy="11" r="1.5"/><path d="M9 17l3-4 3 4"/></svg></div>
  <div class="label">Site work</div>
</div>
<div class="card" style="left:445px;top:1709px">
  <div class="photo" role="img" aria-label="Worker spreading wet concrete" style="background:linear-gradient(180deg,#7d7a72,#a9a59a)"></div>
  <div class="badge"><svg width="36" height="36" viewBox="0 0 24 24" fill="none" stroke="#111" stroke-width="1.5"><rect x="2" y="8" width="11" height="8" rx="3"/><path d="M13 10h4l4 4v2h-8z"/><circle cx="6" cy="18" r="2"/><circle cx="17" cy="18" r="2"/></svg></div>
  <div class="label">Concrete</div>
</div>
<div class="card" style="left:780px;top:1709px">
  <div class="photo" role="img" aria-label="Aerial view of a winding garden path through lawn" style="background:linear-gradient(135deg,#4f8a2f,#8fbf55)"></div>
  <div class="badge"><svg width="36" height="36" viewBox="0 0 24 24" fill="none" stroke="#111" stroke-width="1.5"><path d="M4 20c4-2 12-2 16 0"/><path d="M12 18V8"/><circle cx="12" cy="7" r="4"/></svg></div>
  <div class="label">Landscaping</div>
</div>
<div class="card" style="left:110px;top:2061px">
  <div class="photo" role="img" aria-label="Excavator demolishing a building" style="background:linear-gradient(180deg,#8fb4d8,#9a8d7b)"></div>
  <div class="badge"><svg width="34" height="34" viewBox="0 0 24 24" fill="none" stroke="#111" stroke-width="1.5"><path d="M6 21V8l6-4 6 4v13z"/><path d="M9 11h2M13 11h2M9 15h2M13 15h2"/></svg></div>
  <div class="label">Demolition</div>
</div>
<div class="card" style="left:445px;top:2061px">
  <div class="photo" role="img" aria-label="Excavator digging a trench in soil" style="background:linear-gradient(180deg,#5f7a3e,#b18a5a)"></div>
  <div class="badge"><svg width="36" height="36" viewBox="0 0 24 24" fill="none" stroke="#111" stroke-width="1.5"><rect x="3" y="14" width="11" height="4" rx="2"/><path d="M8 14v-4h4l2 4"/><path d="M14 10l5-3 2 5h-4"/></svg></div>
  <div class="label">Trenching</div>
</div>
<div class="card" style="left:780px;top:2061px">
  <div class="photo" role="img" aria-label="Technician servicing an elevator shaft" style="background:linear-gradient(180deg,#8e9498,#5d6368)"></div>
  <div class="badge"><svg width="34" height="34" viewBox="0 0 24 24" fill="none" stroke="#111" stroke-width="1.5"><rect x="4" y="3" width="16" height="18"/><path d="M12 3v18M8 7h0M16 7h0"/></svg></div>
  <div class="label">Elevator</div>
</div>
<a class="btn" style="left:509px;top:2431px;width:174px;height:45px">View More</a>

<section class="abs portfolio">
  <svg width="1200" height="140" viewBox="0 0 1200 140">
    <path fill="#fff" d="M0 0 H1200 V0 C 1000 110, 620 150, 0 8 Z"/>
  </svg>
</section>
<h2 class="section-title" style="top:2710px;color:#fff">OUR PORTFOLIO</h2>
<div class="pf-photo" style="left:152px;top:2799px;width:405px;background:linear-gradient(180deg,#5e7fa0,#2e3d4d 70%,#c79a6a)" role="img" aria-label="Modern glass office building at sunset"></div>
<div class="pf-photo" style="left:636px;top:2799px;width:404px;background:linear-gradient(180deg,#d7e4ee,#7f9fb8 55%,#4d7a3d)" role="img" aria-label="Glass office towers behind a tree-lined plaza"></div>
<div class="pf-caption" style="left:175px;top:3090px">Job Order Contract (JOC) | 2016-2023 | County of Ridgemont</div>
<div class="pf-caption" style="left:659px;top:3090px">IDIQ/JOC 3-year Contract | Coastal Facilities Command</div>
<div class="arrow" style="left:15px;top:2916px"><svg width="22" height="22" viewBox="0 0 24 24" fill="none" stroke="#12a5e6" stroke-width="3"><path d="M15 5l-7 7 7 7"/></svg></div>
<div class="arrow" style="left:1120px;top:2916px"><svg width="22" height="22" viewBox="0 0 24 24" fill="none" stroke="#12a5e6" stroke-width="3"><path d="M9 5l7 7-7 7"/></svg></div>

<h2 class="section-title" style="top:3367px">OUR TESTIMONIALS</h2>
<div class="quote-card" style="left:89px">
  <div class="quote-mark"><svg width="40" height="34" viewBox="0 0 40 34" fill="#fff"><path d="M2 34V20C2 8 8 2 17 0v6c-5 2-7 6-7 10h7v18zM23 34V20c0-12 6-18 15-20v6c-5 2-7 6-7 10h7v18z"/></svg></div>
  <p class="quote-text">Lorem Ipsum is simply dummy text of the printing and typesetting industry. Lorem Ipsum has been the industry's standard dummy text ever since the</p>
  <div class="quote-name">Marissa Cole</div>
  <div class="quote-loc">Newyork</div>
</div>
<div class="quote-card" style="left:437px">
  <div class="quote-mark"><svg width="40" height="34" viewBox="0 0 40 34" fill="#fff"><path d="M2 34V20C2 8 8 2 17 0v6c-5 2-7 6-7 10h7v18zM23 34V20c0-12 6-18 15-20v6c-5 2-7 6-7 10h7v18z"/></svg></div>
  <p class="quote-text">Lorem Ipsum is simply dummy text of the printing and typesetting industry. Lorem Ipsum has been the industry's standard dummy text ever since the</p>
  <div class="quote-name">Dan</div>
  <div class="quote-loc">Florida</div>
</div>
<div class="quote-card" style="left:785px">
  <div class="quote-mark"><svg width="40" height="34" viewBox="0 0 40 34" fill="#fff"><path d="M2 34V20C2 8 8 2 17 0v6c-5 2-7 6-7 10h7v18zM23 34V20c0-12 6-18 15-20v6c-5 2-7 6-7 10h7v18z"/></svg></div>
  <p class="quote-text">Lorem Ipsum is simply dummy text of the printing and typesetting industry. Lorem Ipsum has been the industry's standard dummy text ever since the</p>
  <div class="quote-name">Priya</div>
  <div class="quote-loc">London</div>
</div>
<div class="abs dots"><span class="on"></span><span></span><span></span><span></span></div>

<footer class="abs footer"></footer>
<div class="abs foot-brand"><i></i>R W Builders</div>
<div class="foot-col"><h4 style="left:398px">Main Links</h4></div>
<ul class="foot-links" style="left:400px"><li>Home</li><li>About Us</li><li>Services</li><li>Portfolio</li><li>Testimonials</li><li>Contact</li></ul>
<div class="foot-col"><h4 style="left:631px">Other Links</h4></div>
<ul class="foot-links" style="left:633px"><li>Privacy Policy</li><li>Terms and Condition</li><li>Legal information</li></ul>
<div class="foot-col"><h4 style="left:882px">Contact Details</h4></div>
<div class="contact-list">
  <b><svg width="14" height="14" viewBox="0 0 24 24"><path fill="#fff" d="M6.6 10.8a15 15 0 0 0 6.6 6.6l2.2-2.2a1 1 0 0 1 1-.25 11.4 11.4 0 0 0 3.6.57 1 1 0 0 1 1 1V20a1 1 0 0 1-1 1A17 17 0 0 1 3 4a1 1 0 0 1 1-1h3.5a1 1 0 0 1 1 1c0 1.25.2 2.45.57 3.57a1 1 0 0 1-.25 1z"/></svg>Call Us</b>
  <div>(805) 555-0142</div>
  <b><svg width="14" height="14" viewBox="0 0 24 24"><path fill="#fff" d="M2 5h20v14H2z"/><path d="M2 5l10 8 10-8" stroke="#0b1a33" stroke-width="2" fill="none"/></svg>Mail Us</b>
  <div>info@rwbuilders.biz</div>
  <b><svg width="14" height="14" viewBox="0 0 24 24" fill="none" stroke="#fff" stroke-width="2"><circle cx="12" cy="12" r="10"/><path d="M2 12h20M12 2c3 3 3 17 0 20M12 2c-3 3-3 17 0 20"/></svg>Website</b>
  <div>www.rwbuilders.biz</div>
  <b><svg width="14" height="14" viewBox="0 0 24 24"><path fill="#fff" d="M12 2a7 7 0 0 0-7 7c0 5 7 13 7 13s7-8 7-13a7 7 0 0 0-7-7zm0 9.5A2.5 2.5 0 1 1 12 6.5a2.5 2.5 0 0 1 0 5z"/></svg>Location</b>
  <div>P.O. Box 4821</div>
  <div>Oak Valley, CA 93400</div>
</div>
<div class="abs rule"></div>
<div class="abs copyright">© 2024 &nbsp;R W Builders &nbsp;I All Rights Reserved</div>

</body>
</html>
```